Concierge Healthcare Business Card Design and Logo

We need a logo and business card design for a new company called "Sound Haven". We will provide concierge audiological care, hearing aids, hearing exams, custom hearing protection etc to patients in the comfort of their homes and offices. We would like a sleek and modern design preferably with an Ear related logo.

Target Market(s)

People with hearing loss, Hunters, Musicians
My usual clientele are older individuals so usually 50+ years old

Industry/Entity Type

Health Care

Contact Information for Business Card

Celia Brandt, AuD
Audiologist
512-648-2917
soundhaven@mailvoro.com
www.soundhaven-vorel.com

Logo Text

Sound Haven

Number of Pages Required

3 page

```html
<!DOCTYPE html>
<html lang="en">
<head>
<meta charset="utf-8">
<title>Sound Haven – Business Card</title>
<link rel="stylesheet" href="https://fonts.googleapis.com/css2?family=PT+Sans:wght@400;700&family=Questrial&display=swap">
<style>
  :root {
    --page-bg: #ecebe9;
    --card-blue: #0a90dc;
    --card-black: #000000;
    --card-white: #ffffff;
    --ink: #111111;
    --text-on-blue: #ffffff;
  }
  * { margin: 0; padding: 0; box-sizing: border-box; }
  html, body {
    width: 1200px; height: 900px; overflow: hidden;
    background: var(--page-bg);
  }
  .canvas { position: relative; width: 1200px; height: 900px; }

  .card {
    position: absolute;
    box-shadow: 0 6px 18px rgba(0,0,0,0.12);
    overflow: hidden;
  }

  /* Front */
  .card-front {
    left: 238px; top: 61px; width: 555px; height: 344px;
    background: var(--card-blue);
    font-family: "PT Sans", sans-serif;
    color: var(--text-on-blue);
  }
  .card-front .dark-band {
    position: absolute; top: 0; right: 0; bottom: 0; width: 93px;
    background: var(--card-black);
  }
  .holder-name {
    position: absolute; left: 33px; top: 56px;
    font-size: 21px; font-weight: 700; line-height: 1;
  }
  .holder-title {
    position: absolute; left: 33px; top: 82px;
    font-size: 15px; line-height: 1;
  }
  .address {
    position: absolute; left: 32px; top: 179px;
    font-size: 15px; line-height: 20px;
  }
  .contact-list {
    position: absolute; left: 33px; top: 228px;
    list-style: none; font-size: 15px; line-height: 20px;
  }
  .contact-list li { display: flex; align-items: center; gap: 9px; }
  .contact-list svg { width: 13px; height: 13px; fill: var(--text-on-blue); flex: none; }

  /* Back */
  .card-back {
    left: 457px; top: 518px; width: 560px; height: 343px;
    background: var(--card-white);
    display: flex; align-items: center; justify-content: center; gap: 14px;
  }
  .brand-name {
    font-family: "Questrial", sans-serif;
    font-size: 41px; color: var(--ink); letter-spacing: 0.5px;
    padding-top: 20px;
  }
  .brand-dot {
    width: 30px; height: 30px; border-radius: 50%;
    background: var(--card-blue); margin-top: 14px;
  }
</style>
</head>
<body>
<main class="canvas">
  <section class="card card-front" aria-label="Business card front">
    <div class="dark-band"></div>
    <p class="holder-name">Celia Brandt, AuD</p>
    <p class="holder-title">Audiologist</p>
    <p class="address">2210 Lamar Crest Blvd<br>Austin, TX 78704</p>
    <ul class="contact-list">
      <li>
        <svg viewBox="0 0 24 24" aria-hidden="true"><path d="M6.6 10.8a15.2 15.2 0 0 0 6.6 6.6l2.2-2.2c.3-.3.7-.4 1-.2 1.1.4 2.3.6 3.6.6.6 0 1 .4 1 1V20c0 .6-.4 1-1 1A17 17 0 0 1 3 4c0-.6.4-1 1-1h3.5c.6 0 1 .4 1 1 0 1.3.2 2.5.6 3.6.1.3 0 .7-.2 1z"/></svg>
        512-648-2917
      </li>
      <li>
        <svg viewBox="0 0 24 24" aria-hidden="true"><path d="M3 6h18v12H3z"/><path d="M3 6l9 7 9-7" stroke="#0a90dc" stroke-width="1.8" fill="none"/></svg>
        soundhaven@mailvoro.com
      </li>
      <li>
        <svg viewBox="0 0 24 24" aria-hidden="true"><circle cx="12" cy="12" r="10"/><path d="M2 12h20M12 2c3 3 3 17 0 20M12 2c-3 3-3 17 0 20" stroke="#0a90dc" stroke-width="1.4" fill="none"/></svg>
        www.soundhaven-vorel.com
      </li>
    </ul>
  </section>

  <section class="card card-back" aria-label="Business card back">
    <span class="brand-name">Sound Haven</span>
    <span class="brand-dot" aria-hidden="true"></span>
  </section>
</main>
</body>
</html>
```